NZ First of it's kind solutions directory and marketplace for busy Mums needs a business card design

We need a business card design for our new nationwide business in NZ (long term plans to go global). We provide solutions to the everyday challenges that busy Mums face by connecting them with quality communities and suppliers of carefully selected, relevant products and services. We sell direct via our online marketplace. The final design should communicate our values of inclusivity, quality and smart solutions. Colours should incorporate our logo colour palette of #477077 and #6ba8b2. Our website is at https://www.brightnestmums.example

Target Market(s)

busy Mums, Age 28 – 50, female, income over $100K, location main centres NZ primarily but NZ wide. Is likely juggling work or career with a young family. Probably had hobbies which have fallen by the wayside.
-Wants to succeed in her chosen career without compromising on family life
-to successfully juggle her career without feeling like she is compromising her children
- Is time poor, something always has to give and it’s generally her health (she’ll stay up late, get stressed)
- probably ex corporate or professional career. Has discretional income

Industry/Entity Type

Business

Contact Information for Business Card

Lena Forbisher, Founder, BrightNestMums.example (Strapline Tap; Gather; Sorted), 47 Kowhai Terrace, Ellerslie, Auckland 1051, New Zealand. Mob: 021 483 517 Ph: +64 (0)9 571 4860

Font styles to use
Other font styles liked:
• Raleway, and/or Architects Daughter

Colors
00a990
33b8a4
86cfc6
cfeae6

Requirements
Must have
• the above details, streamline. the logo and colours associated with those logos
Should not have
• foil or metallic colours

```html
<!DOCTYPE html>
<html lang="en">
<head>
<meta charset="utf-8">
<title>BrightNestMums business card</title>
<link rel="stylesheet" href="https://fonts.googleapis.com/css2?family=Arimo:wght@400;700&display=swap">
<style>
  :root {
    --page-bg: #e9e7e4;
    --card-black: #0d0d0d;
    --brand-dark: #477077;
    --brand-light: #6ba8b2;
    --text-white: #f2f2f2;
    --text-silver: #cfcfcf;
    --divider: #2c2c2c;
  }
  * { margin: 0; padding: 0; box-sizing: border-box; }
  html, body {
    width: 1200px;
    height: 900px;
    overflow: hidden;
    background: var(--page-bg);
    font-family: "Arimo", Arial, sans-serif;
  }
  .sheet {
    position: relative;
    width: 1200px;
    height: 900px;
  }
  .card {
    position: absolute;
    top: 290px;
    width: 525px;
    height: 300px;
    background: var(--card-black);
    border-radius: 4px;
    box-shadow: 0 6px 18px rgba(0,0,0,0.25);
  }
  .card--front { left: 55px; }
  .card--back { left: 620px; }

  /* front */
  .brand-block {
    position: absolute;
    left: 28px;
    top: 0;
    width: 230px;
    height: 100%;
    display: flex;
    align-items: center;
    gap: 10px;
  }
  .brand-dot {
    width: 22px;
    height: 22px;
    border-radius: 50%;
    background: var(--brand-dark);
    flex: none;
  }
  .brand-name {
    font-size: 24px;
    font-weight: 700;
    color: var(--brand-dark);
    letter-spacing: 0.2px;
  }
  .divider {
    position: absolute;
    left: 268px;
    top: 70px;
    width: 1px;
    height: 160px;
    background: var(--divider);
  }
  .details {
    position: absolute;
    left: 290px;
    top: 72px;
    color: var(--text-white);
    font-size: 14px;
    line-height: 1.3;
  }
  .person-name {
    font-size: 19px;
    font-weight: 700;
    color: var(--brand-light);
    text-transform: uppercase;
    letter-spacing: 0.3px;
  }
  .person-role {
    font-size: 13px;
    margin-bottom: 14px;
  }
  .contact-list { list-style: none; margin-bottom: 12px; }
  .contact-list li {
    display: flex;
    align-items: center;
    gap: 7px;
    font-size: 14px;
    line-height: 1.45;
  }
  .contact-icon { width: 11px; height: 11px; flex: none; }
  .address { font-size: 14px; line-height: 1.35; }

  /* back */
  .back-mark {
    position: absolute;
    inset: 0;
    display: flex;
    align-items: center;
    justify-content: center;
    gap: 12px;
  }
  .back-mark .brand-dot {
    width: 30px;
    height: 30px;
    background: var(--text-silver);
  }
  .back-mark .brand-name {
    font-size: 36px;
    color: var(--text-silver);
  }
</style>
</head>
<body>
<main class="sheet">

  <section class="card card--front" aria-label="Business card front">
    <div class="brand-block">
      <span class="brand-dot"></span>
      <span class="brand-name">BrightNestMums</span>
    </div>
    <div class="divider"></div>
    <div class="details">
      <p class="person-name">Lena Forbisher</p>
      <p class="person-role">Managing Director</p>
      <ul class="contact-list">
        <li>
          <svg class="contact-icon" viewBox="0 0 12 12" aria-hidden="true"><path d="M1 4c0-2 2-3 5-3s5 1 5 3l-2 1-1-1H4L3 5zM3 6h6l1 5H2z" fill="#f2f2f2"/></svg>
          021 483 517
        </li>
        <li>
          <svg class="contact-icon" viewBox="0 0 12 12" aria-hidden="true"><rect x="2.5" y="0.5" width="7" height="11" rx="1" fill="none" stroke="#f2f2f2"/><rect x="4" y="2" width="4" height="6" fill="#f2f2f2"/></svg>
          +64 (0)9 571 4860
        </li>
        <li>
          <svg class="contact-icon" viewBox="0 0 12 12" aria-hidden="true"><circle cx="6" cy="6" r="5.5" fill="#f2f2f2"/><path d="M3 4h3v2H4zM7 7h2v2H7z" fill="#0d0d0d"/></svg>
          www.BrightNestMums.example
        </li>
      </ul>
      <p class="address">47 Kowhai Terrace, Ellerslie<br>Auckland 1051, New Zealand</p>
    </div>
  </section>

  <section class="card card--back" aria-label="Business card back">
    <div class="back-mark">
      <span class="brand-dot"></span>
      <span class="brand-name">BrightNestMums</span>
    </div>
  </section>

</main>
</body>
</html>
```